Policies Manual Design & Formatting

My company currently has complete bylaws and policies organized as needed. We would like them formatted in Word to look professional and easily editable.

We have all text and titles completed and a brand book to guide text and colors. We would also like the designer to gather design inspiration from our website brackenvalecouncil.org.

Text word file upload coming on 10/18
Updates

Went on vacation/holiday

Industry/Entity Type

Business Consultant

Font styles to use
Serif
Sans Serif
Other font styles liked:
• Montserrat and Domine

Colors

Designer to choose colors to be used in the design.

Requirements
Must have
• Montserrat and domine fonts
• Colors from brand book file
• layout and print formatting
• dynamic Table of Contents
• Incorporate logo and company information
• Include automatic page numbers
• Modify or add headers/footer
• Profeasional cover page

```html
<!DOCTYPE html>
<html lang="en">
<head>
<meta charset="utf-8">
<title>Bylaws – Membership</title>
<link href="https://fonts.googleapis.com/css2?family=Domine:wght@700&family=Montserrat:wght@400;800&display=swap" rel="stylesheet">
<style>
  :root {
    --page: #ffffff;
    --ink: #1c1c1c;
    --accent: #1b96c8;
    --folio: #ffffff;
  }
  html, body {
    margin: 0;
    padding: 0;
    width: 846px;
    height: 1200px;
    overflow: hidden;
    background: var(--page);
  }
  .page {
    position: relative;
    width: 846px;
    height: 1200px;
    background: var(--page);
    color: var(--ink);
  }
  .side-band {
    position: absolute;
    top: 0;
    left: 672px;
    width: 70px;
    height: 1200px;
    background: var(--accent);
  }
  .folio {
    position: absolute;
    left: 672px;
    width: 70px;
    top: 1126px;
    text-align: center;
    font-family: "Montserrat", sans-serif;
    font-weight: 800;
    font-size: 22px;
    color: var(--folio);
  }
  .content {
    position: absolute;
    left: 79px;
    top: 78px;
    width: 590px;
  }
  .section-title {
    font-family: "Domine", serif;
    font-weight: 700;
    font-size: 16.5px;
    line-height: 21px;
    margin: 0 0 20px;
    letter-spacing: -0.2px;
  }
  .clause {
    font-family: "Montserrat", sans-serif;
    font-weight: 400;
    font-size: 16.4px;
    line-height: 21.4px;
    margin: 0 0 20px;
    white-space: nowrap;
  }
  .clause + .section-title { margin-top: 0; }
</style>
</head>
<body>
<div class="page">
  <main class="content">
    <h2 class="section-title">2.3: Application</h2>
    <p class="clause">Application for membership shall be submitted through the<br>Chamber's website or by paper application at the Chamber office.</p>
    <p class="clause">The Board of Directors may from time to time prescribe or modify<br>the content of the application, as well as dues associated with each<br>type of membership, but if not so prescribed, such application shall<br>contain the name, physical address, mailing address, email<br>address, and telephone number of such prospective member and,<br>if the application is one for active membership, the individual<br>authorized as the voting representative for the prospective<br>member.</p>

    <h2 class="section-title">2.4: Acceptance</h2>
    <p class="clause">Acceptance of members shall be made by the Board of Directors<br>at the next regular Board meeting, after receipt of an application<br>for membership. Any acceptance of an applicant for membership<br>is made on the condition that the applicant accepts the terms and<br>conditions of membership and agrees to abide by these bylaws.</p>

    <h2 class="section-title">2.5: Denial and Revocation of Application</h2>
    <p class="clause">Denial or revocation of any application for membership must be<br>based on cause and shall be determined by the Board of Directors<br>in an executive session, after an evaluation of the applicant’s ability<br>and willingness to abide by the purposes of the Chamber, the<br>terms and conditions of membership, and these bylaws. Matters<br>considered by the Board in making their determination shall be<br>recorded, sealed and maintained by the Secretary of theBoard . A<br>two-thirds majority is required to deny or revoke an application or<br>membership. If an application for membership is denied, the<br>Chamber shall return to the applicant all dues, if any, that the<br>applicant paid with the submission of the application. If a<br>membership is revoked, all dues paid shall not be refunded.</p>

    <h2 class="section-title">2.6: Membership Dues</h2>
    <p class="clause">Dues for active and affiliate members shall be at such rate or rates,<br>schedule or formula as prescribed by the Board. The Board may<br>modify all such dues as it deems appropriate upon a majority vote.<br>Annual membership dues are billed annually and due 30 days after<br>invoiced.</p>
  </main>
  <div class="side-band"></div>
  <div class="folio">4</div>
</div>
</body>
</html>
```